Bright Step Path Flyer, eyecatching

Hi,
To give you an idea of the business for design purposes, #BrighttStepPath is predominantly a recruitment and people development business, ran by me dedicated to training & assisting others in achieving extra income (pt or f/t) around their current commitments, people also have the opportunity to build their own business brand with my support. My brand colours are Red, White and Black, and I would like to incorporate the following text;

#BrightStepPath

Recruiting now! Start today & start earning!

Would you like an extra income, for…
A holiday?…A new car?…Lifestyle changes?
(Can you put a tick box or something similar adjacent to each)

Are you facing…
Redundancy? Birth of a new child? Hefty bills?

If so, I have the solution.

Contact Yvonne Darcott today: (can you insert the appropriate icon for each of the contact details)
Tel: 07419 604172
Twitter: @Bright_StepPath
Email: Yvonne@brightsteppath-example.co.uk
Facebook: www.circlepage-example.com/yvonbrightsteppath

Target Market(s)

Women aged 25-45 years, possibly busy mums too, wanting to earn additinal income to allow them more choices, be it family time, money, new challenge, meeting new people, personal development

Industry/Entity Type

Health And Wellness

Font styles to use
Serif
Sans Serif
Decorative
Script

Colors
ec1f27
ffffff
000000

Requirements
Must have
• My heels logo, be clear concise and eye catching, I also have the following strap line if you wish to use;
• Empowering other to achieve
• Also I have attached a closeup picture of myself but would ideally only like half my face to appear (leftside) similar to the other picture posted - if you can
Nice to have
• Perhaps adding other forms of graphics, or the 3rd picture I have attached with myself...possibly just the shoes though
Should not have
• Too many colours

```html
<!DOCTYPE html>
<html lang="en">
<head>
<meta charset="utf-8">
<title>Bright Step Path – Recruiting Flyer</title>
<link rel="stylesheet" href="https://fonts.googleapis.com/css2?family=Oswald:wght@400;500;600;700&family=Roboto:ital,wght@0,400;0,500;0,700;1,700&display=swap">
<style>
  :root {
    --brand-red: #ec1f27;
    --deep-red: #b3121a;
    --ink: #000000;
    --paper: #ffffff;
    --paper-shade: #e9e9e9;
    --bar: #0b0b0b;
    --soft-text: #f2f2f2;
  }
  * { box-sizing: border-box; margin: 0; padding: 0; }
  html, body { width: 900px; height: 1200px; overflow: hidden; background: var(--paper); }
  .flyer { position: relative; width: 900px; height: 1200px; overflow: hidden; font-family: "Roboto", Arial, sans-serif; }
  .flyer-shapes, .portrait { position: absolute; left: 0; top: 0; }
  .abs { position: absolute; }

  .brand-mark {
    left: 470px; top: 120px; width: 410px; text-align: center;
    font-family: "Oswald", sans-serif; font-weight: 600; font-size: 48px;
    color: var(--ink); letter-spacing: 1px; text-transform: uppercase; line-height: 1.1;
  }
  .brand-band-name {
    left: 32px; top: 536px;
    font-family: "Oswald", sans-serif; font-weight: 700; font-size: 40px;
    color: var(--paper); letter-spacing: 0.5px; line-height: 1;
  }
  .recruiting {
    left: 34px; top: 636px;
    font-family: "Oswald", sans-serif; font-weight: 500; font-size: 58px;
    color: var(--brand-red); line-height: 1; transform: scaleX(0.86); transform-origin: left;
  }
  .divider { left: 38px; top: 721px; width: 332px; height: 4px; background: var(--ink); }
  .start-today {
    left: 34px; top: 746px;
    font-family: "Oswald", sans-serif; font-weight: 500; font-size: 76px;
    color: var(--ink); line-height: 1; transform: scaleX(0.86); transform-origin: left;
  }
  .start-earning {
    left: 36px; top: 824px;
    font-family: "Oswald", sans-serif; font-weight: 500; font-size: 56px;
    color: var(--brand-red); line-height: 1; transform: scaleX(0.86); transform-origin: left;
  }

  .panel-heading {
    right: 74px; text-align: right;
    font-family: "Oswald", sans-serif; font-weight: 500; font-size: 34px;
    color: var(--paper); line-height: 1; transform: scaleX(0.9); transform-origin: right;
  }
  .offer-item {
    right: 110px; text-align: right;
    font-family: "Roboto", Arial, sans-serif; font-style: italic; font-weight: 700; font-size: 30px;
    color: var(--paper); line-height: 1;
  }
  .solution {
    left: 479px; top: 950px; width: 327px; text-align: center;
    font-family: "Roboto", Arial, sans-serif; font-weight: 500; font-size: 25px;
    color: var(--paper); line-height: 1; letter-spacing: 0.3px;
  }

  .contact-heading {
    left: 38px; top: 988px;
    font-family: "Roboto", Arial, sans-serif; font-weight: 700; font-size: 19px;
    color: var(--paper);
  }
  .contact-list { left: 38px; top: 1036px; list-style: none; }
  .contact-item {
    display: flex; align-items: center; gap: 10px; height: 28px;
    font-size: 21px; color: var(--soft-text);
  }
  .contact-icon { width: 18px; height: 18px; flex: none; }
</style>
</head>
<body>
<main class="flyer">

  <svg class="flyer-shapes" width="900" height="1200" viewBox="0 0 900 1200" aria-hidden="true">
    <defs>
      <radialGradient id="paper-glow" cx="0.5" cy="0.45" r="0.7">
        <stop offset="0" stop-color="#ffffff"/>
        <stop offset="1" stop-color="#e4e4e4"/>
      </radialGradient>
      <linearGradient id="red-panel" x1="0" y1="0" x2="1" y2="0">
        <stop offset="0" stop-color="#c3151c"/>
        <stop offset="0.45" stop-color="#ec1f27"/>
        <stop offset="1" stop-color="#a80f16"/>
      </linearGradient>
      <linearGradient id="red-band" x1="0" y1="0" x2="1" y2="0">
        <stop offset="0" stop-color="#b3121a"/>
        <stop offset="0.5" stop-color="#ec1f27"/>
        <stop offset="1" stop-color="#d41a22"/>
      </linearGradient>
    </defs>

    <rect class="paper" width="900" height="1200" fill="url(#paper-glow)"/>

    <path class="offer-panel" d="M405,330 C550,290 720,300 900,300 L900,1200 L520,1200 L520,1010 C460,990 420,930 405,880 Z" fill="url(#red-panel)"/>
    <path class="offer-panel-edge" d="M405,330 C550,290 720,300 900,300" fill="none" stroke="var(--ink)" stroke-width="10"/>

    <path class="name-band" d="M0,482 C130,470 280,470 405,445 L405,622 C270,600 120,600 0,618 Z" fill="url(#red-band)"/>
    <path class="name-band-edge" d="M0,482 C130,470 280,470 405,445" fill="none" stroke="var(--ink)" stroke-width="8"/>

    <g class="offer-bars" fill="var(--bar)">
      <rect x="403" y="488" width="497" height="42"/>
      <rect x="403" y="542" width="497" height="41"/>
      <rect x="403" y="592" width="497" height="41"/>
      <rect x="403" y="744" width="497" height="42"/>
      <rect x="403" y="798" width="497" height="41"/>
      <rect x="403" y="849" width="497" height="41"/>
    </g>

    <g class="ticks" fill="none" stroke="var(--brand-red)" stroke-width="5" stroke-linecap="round" stroke-linejoin="round">
      <path d="M803,511 L811,521 L829,496"/>
      <path d="M803,564 L811,574 L829,549"/>
      <path d="M803,614 L811,624 L829,599"/>
      <path d="M803,767 L811,777 L829,752"/>
      <path d="M803,820 L811,830 L829,805"/>
      <path d="M803,871 L811,881 L829,856"/>
    </g>

    <g class="solution-rules" stroke="var(--ink)" stroke-width="3">
      <line x1="479" y1="940" x2="806" y2="940"/>
      <line x1="479" y1="992" x2="806" y2="992"/>
    </g>

    <path class="footer-edge" d="M0,944 C300,944 560,1024 900,1074" fill="none" stroke="var(--brand-red)" stroke-width="8"/>
    <path class="footer" d="M0,950 C300,950 560,1030 900,1080 L900,1200 L0,1200 Z" fill="var(--ink)"/>
    <line class="contact-rule" x1="0" y1="1019" x2="372" y2="1019" stroke="var(--brand-red)" stroke-width="3"/>
  </svg>

  <svg class="portrait" width="460" height="480" viewBox="0 0 460 480" role="img" aria-label="Close-up portrait photo of Yvonne Darcott">
    <defs>
      <radialGradient id="portrait-tone" cx="0.45" cy="0.45" r="0.65">
        <stop offset="0" stop-color="#e6c2ae"/>
        <stop offset="0.6" stop-color="#eddcc6"/>
        <stop offset="1" stop-color="#f4ecdf"/>
      </radialGradient>
    </defs>
    <circle cx="225" cy="238" r="228" fill="url(#portrait-tone)" stroke="var(--brand-red)" stroke-width="6"/>
  </svg>

  <div class="abs brand-mark">Bright Step Path</div>

  <div class="abs brand-band-name">BRIGHT STEP PATH</div>
  <div class="abs recruiting">Recruiting now!</div>
  <div class="abs divider"></div>
  <div class="abs start-today">START TODAY</div>
  <div class="abs start-earning">START EARNING!</div>

  <div class="abs panel-heading" style="top:402px">Would you like an extra income</div>
  <div class="abs panel-heading" style="top:446px">for…</div>
  <div class="abs offer-item" style="top:494px">A holiday?…</div>
  <div class="abs offer-item" style="top:548px">A new car?…</div>
  <div class="abs offer-item" style="top:597px">Lifestyle changes?</div>

  <div class="abs panel-heading" style="top:684px">Are you facing…</div>
  <div class="abs offer-item" style="top:750px">Redundancy?</div>
  <div class="abs offer-item" style="top:804px">Birth of a new child?</div>
  <div class="abs offer-item" style="top:855px">Hefty bills?</div>

  <div class="abs solution">If so, I have the solution</div>

  <div class="abs contact-heading">Contact Yvonne Darcott today:</div>
  <ul class="abs contact-list">
    <li class="contact-item">
      <svg class="contact-icon" viewBox="0 0 18 18" aria-hidden="true"><circle cx="9" cy="9" r="8" fill="none" stroke="var(--brand-red)" stroke-width="1.5"/><path d="M6,4.5 L7.5,4.5 L8.3,7 L7.2,8 C7.8,9.3 8.7,10.2 10,10.8 L11,9.7 L13.5,10.5 L13.5,12 C13.5,12.8 12.8,13.5 12,13.5 C8.4,13.2 4.8,9.6 4.5,6 C4.5,5.2 5.2,4.5 6,4.5 Z" fill="var(--brand-red)"/></svg>
      <span>07419 604172</span>
    </li>
    <li class="contact-item">
      <svg class="contact-icon" viewBox="0 0 18 18" aria-hidden="true"><rect x="1" y="1" width="16" height="16" fill="var(--brand-red)"/></svg>
      <span>@Bright_StepPath</span>
    </li>
    <li class="contact-item">
      <svg class="contact-icon" viewBox="0 0 18 18" aria-hidden="true"><rect x="1" y="3.5" width="16" height="11" fill="var(--brand-red)"/><path d="M1.5,4 L9,10 L16.5,4" fill="none" stroke="var(--ink)" stroke-width="1.4"/></svg>
      <span>Yvonne@brightsteppath-example.co.uk</span>
    </li>
    <li class="contact-item">
      <svg class="contact-icon" viewBox="0 0 18 18" aria-hidden="true"><rect x="2" y="2" width="14" height="14" fill="var(--brand-red)"/></svg>
      <span>www.circlepage-example.com/yvonbrightsteppath</span>
    </li>
  </ul>

</main>
</body>
</html>
```